Brackwell Yard Services Flyer Design

I need a new flyer design for my business, Brackwell Yard Services. I’ll be providing my old flyer and logo as references. The new flyer should feature updated wording, contact information, logos, and photos, but still keep the original “What We Do” section and include the phrase “Don’t See? Just Ask!” somewhere near the services. The flyer needs to look great in black and white for door-to-door handouts but also be eye-catching and professional enough for social media use.

The updated content should include the headline “Transforming Outdoor Spaces with Hard Work & Precision” and highlight three main service areas: Landscaping Services (project-based landscaping to clean, prepare, and transform outdoor spaces with precision), Property Cleanup (quick hauls, debris removal, or full cleanouts—no job too big or small), and Ground Preparation (pad preparation, brush removal, and fire lines—making properties safe, functional, and project-ready).

Please also include a “Why Choose Us?” section that lists: Locally owned since 2022, Reliable & affordable – no corners cut, Professional results you can trust, LICENSED AND Insured, and Quality work / on time / references / flexible / follow-up.

At the bottom, include the contact details: Call or Text Today!
www.brackwellyard.example
| sales@brackwellyard.example
| (555) 014-7293

The overall design should be clean, professional, and easy to read with a layout that clearly shows what we offer. Use visuals that represent outdoor services, landscaping, and property cleanup/prep work. I want something that feels trustworthy, family-friendly, and modern.
Use the same photo of leaf clean up from the original flyer if possible.
Our company colors are also black and white. For the most part.

```html
<!DOCTYPE html>
<html lang="en">
<head>
<meta charset="utf-8">
<title>Brackwell Yard Services Flyer</title>
<link href="https://fonts.googleapis.com/css2?family=Archivo:wdth,wght@62..125,400..900&family=Roboto+Condensed:ital,wght@0,400..900;1,400..900&display=swap" rel="stylesheet">
<style>
  :root {
    --ink: #000000;
    --paper: #ffffff;
    --soft-grey: #d9d9d9;
    --rule-grey: #8a8a8a;
    --hero-dark-1: #2a2620;
    --hero-dark-2: #3b3a2c;
    --leaf-green: #6f8f2a;
    --leaf-orange: #b5621c;
    --leaf-brown: #6b3a14;
  }
  * { box-sizing: border-box; margin: 0; padding: 0; }
  html, body { width: 900px; height: 1200px; overflow: hidden; background: var(--ink); }
  .flyer {
    position: relative; width: 900px; height: 1200px; overflow: hidden;
    background: var(--ink); color: var(--paper);
    font-family: "Roboto Condensed", "Arial Narrow", sans-serif;
  }
  .abs { position: absolute; }

  /* Hero */
  .hero-backdrop {
    left: 0; top: 0; width: 900px; height: 473px;
    background: linear-gradient(160deg, var(--hero-dark-2) 0%, var(--hero-dark-1) 55%, #1d1b17 100%);
  }
  .brand {
    left: 59px; top: 40px; font-family: "Archivo", sans-serif;
    font-variation-settings: "wdth" 125; font-weight: 800; color: var(--paper);
    line-height: 1; text-transform: uppercase;
  }
  .brand-main { font-size: 27px; letter-spacing: 1px; display: block; }
  .brand-sub { font-size: 13px; letter-spacing: 2px; display: block; margin-top: 4px; }
  .headline { left: 52px; top: 120px; width: 500px; height: 270px; }
  .headline text {
    font-family: "Archivo", sans-serif; font-variation-settings: "wdth" 125;
    font-weight: 900; fill: var(--paper);
  }
  .hero-photo { left: 550px; top: 0; width: 350px; height: 473px; }

  /* Why choose us */
  .why-panel {
    left: 0; top: 403px; width: 377px; height: 251px; background: var(--paper);
    border-radius: 0 17px 17px 0; color: var(--ink);
  }
  .why-title {
    position: absolute; left: 52px; top: 20px; font-size: 33px;
    font-weight: 900; font-style: italic; line-height: 1;
  }
  .why-list { position: absolute; left: 60px; top: 61px; list-style: none; width: 300px; }
  .why-list li {
    position: relative; padding-left: 18px; font-size: 17px; font-weight: 500;
    line-height: 23.2px;
  }
  .why-list li::before {
    content: ""; position: absolute; left: 1px; top: 7px; width: 8px; height: 8px;
    background: var(--ink); transform: rotate(45deg);
  }
  .ask-line {
    position: absolute; left: 54px; top: 208px; font-size: 27px; font-weight: 900; line-height: 1;
  }

  /* What we do */
  .what-title {
    left: 56px; top: 674px; font-size: 33px; font-weight: 900; font-style: italic; line-height: 1;
  }
  .dotted-rule { height: 4px; border-top: 1px dotted var(--rule-grey); border-bottom: 1px dotted var(--rule-grey); top: 689px; }
  .group-label {
    font-family: "Archivo", sans-serif; font-weight: 500; font-size: 19px;
    letter-spacing: 0.3px; line-height: 1; left: 90px;
  }
  .service-item {
    font-size: 17px; font-weight: 500; line-height: 1; padding-left: 19px;
  }
  .service-item::before {
    content: ""; position: absolute; left: 0; top: 3px; width: 8px; height: 8px;
    background: var(--soft-grey); transform: rotate(45deg);
  }

  /* Service cards */
  .card {
    left: 412px; width: 451px; height: 208px; border: 1.5px solid var(--paper);
    border-radius: 15px; background: var(--ink); overflow: hidden;
  }
  .card-photo {
    position: absolute; left: 3px; top: 3px; width: 257px; height: 199px;
    border-radius: 12px 0 0 12px;
  }
  .card-head {
    position: absolute; left: 279px; top: 20px; font-size: 20px; font-weight: 900;
    font-style: italic; line-height: 21px; text-transform: uppercase;
  }
  .card-body {
    position: absolute; left: 260px; top: 84px; right: 3px; bottom: 3px;
    background: var(--paper); color: var(--ink); border-radius: 0 0 12px 0;
  }
  .card-body p {
    position: absolute; left: 42px; top: 10px; font-size: 15px; font-weight: 500; line-height: 17.6px;
  }
  .tick { position: absolute; left: 14px; top: 12px; width: 14px; height: 14px; }

  .photo-patio { background: linear-gradient(180deg, #6c8a4a 0%, #a9b3a6 40%, #c9b9b4 70%, #8d7a63 100%); }
  .photo-debris { background: linear-gradient(170deg, #8a8f7a 0%, #6c6658 35%, #8e8b70 65%, #3b4a5e 100%); }
  .photo-ground { background: linear-gradient(180deg, #a9c6e4 0%, #8d97a3 35%, #9a9a92 55%, #b7ab97 100%); }

  /* Contact */
  .contact-panel {
    left: 0; top: 1104px; width: 410px; height: 96px; background: var(--paper);
    border-radius: 0 40px 0 0; color: var(--ink);
  }
  .call-line {
    position: absolute; left: 21px; top: 10px; font-size: 14px; font-weight: 500;
    display: flex; align-items: center; width: 387px;
  }
  .call-line::after { content: ""; flex: 1; margin-left: 8px; border-top: 1px dashed var(--rule-grey); }
  .contact-row {
    position: absolute; left: 67px; display: flex; align-items: center; gap: 9px;
    font-size: 22px; font-weight: 500; line-height: 1;
  }
  .contact-row svg { width: 14px; height: 14px; }
  .phone-block { left: 488px; top: 1142px; width: 380px; height: 52px; }
  .phone-block text {
    font-family: "Archivo", sans-serif; font-variation-settings: "wdth" 112;
    font-weight: 600; fill: var(--paper);
  }
</style>
</head>
<body>
<main class="flyer">

  <div class="abs hero-backdrop" role="img" aria-label="Darkened photo of a pile of hauled junk and yard debris"></div>

  <div class="abs brand">
    <span class="brand-main">Brackwell</span>
    <span class="brand-sub">Yard Services</span>
  </div>

  <svg class="abs headline" viewBox="0 0 500 270" aria-label="Transforming outdoor spaces with hard work and precision">
    <text x="2" y="33" font-size="40" textLength="427" lengthAdjust="spacingAndGlyphs">TRANSFORMING</text>
    <text x="2" y="102" font-size="60" textLength="425" lengthAdjust="spacingAndGlyphs">OUTDOOR</text>
    <text x="2" y="154" font-size="44" textLength="423" lengthAdjust="spacingAndGlyphs">SPACES WITH</text>
    <text x="2" y="207" font-size="44" textLength="423" lengthAdjust="spacingAndGlyphs">HARD WORK</text>
    <text x="2" y="257" font-size="44" textLength="419" lengthAdjust="spacingAndGlyphs">&amp; PRECISION</text>
  </svg>

  <svg class="abs hero-photo" viewBox="0 0 350 473" role="img" aria-label="Photo of a rake gathering autumn leaves beside a burlap yard waste bag on green grass">
    <defs>
      <linearGradient id="leafTones" x1="0" y1="0" x2="0" y2="1">
        <stop offset="0" stop-color="#4f6b23"/>
        <stop offset="0.4" stop-color="var(--leaf-green)"/>
        <stop offset="0.7" stop-color="var(--leaf-orange)"/>
        <stop offset="1" stop-color="var(--leaf-brown)"/>
      </linearGradient>
    </defs>
    <path d="M177 -4 L20 118 Q11 126 11 138 L11 340 Q11 352 20 360 L193 480 L360 480 L360 -4 Z"
          fill="url(#leafTones)" stroke="var(--paper)" stroke-width="5" stroke-linejoin="round"/>
  </svg>

  <section class="abs why-panel">
    <h2 class="why-title">Why Choose Us?</h2>
    <ul class="why-list">
      <li>Locally owned since 2022</li>
      <li>Reliable &amp; affordable – no corners cut</li>
      <li>Professional results you can trust</li>
      <li>Licensed And Insured</li>
      <li>Quality work / On time / References /<br>Flexible / Follow-up</li>
    </ul>
    <p class="ask-line">Don’t See? Just Ask!</p>
  </section>

  <div class="abs dotted-rule" style="left:0;width:51px;"></div>
  <h2 class="abs what-title">What We Do</h2>
  <div class="abs dotted-rule" style="left:258px;width:152px;"></div>

  <h3 class="abs group-label" style="top:722px;">REMOVE</h3>
  <div class="abs service-item" style="left:96px;top:757px;">Junk removal</div>
  <div class="abs service-item" style="left:96px;top:780px;">Trash &amp; waste hauling</div>
  <div class="abs service-item" style="left:96px;top:803px;">Yard and garden cleanup</div>
  <div class="abs service-item" style="left:96px;top:827px;">Appliance removal</div>

  <h3 class="abs group-label" style="top:861px;">INSTALL</h3>
  <div class="abs service-item" style="left:98px;top:897px;">Mulch</div>
  <div class="abs service-item" style="left:201px;top:897px;">Plants</div>
  <div class="abs service-item" style="left:98px;top:920px;">D.G.</div>
  <div class="abs service-item" style="left:201px;top:920px;">Rock</div>

  <h3 class="abs group-label" style="top:956px;">MAINTENANCE &amp; OTHER</h3>
  <div class="abs service-item" style="left:97px;top:992px;">Yard clean up</div>
  <div class="abs service-item" style="left:97px;top:1015px;">Weed prevention (pre-emergent)</div>
  <div class="abs service-item" style="left:97px;top:1038px;">Roof &amp; gutter cleaning</div>
  <div class="abs service-item" style="left:97px;top:1061px;">Fence &amp; deck staining</div>

  <article class="abs card" style="top:486px;">
    <div class="card-photo photo-patio" role="img" aria-label="Photo of a new paver patio laid beside a house with a green lawn"></div>
    <h3 class="card-head">Landscaping<br>Services</h3>
    <div class="card-body">
      <svg class="tick" viewBox="0 0 14 14"><circle cx="7" cy="7" r="7" fill="var(--ink)"/><path d="M3.8 7.2 L6 9.3 L10.2 4.9" fill="none" stroke="var(--paper)" stroke-width="1.7"/></svg>
      <p>Project-based<br>landscaping to Clean<br>Prepare, and<br>Transform Outdoor<br>Spaces with precision</p>
    </div>
  </article>

  <article class="abs card" style="top:704px;">
    <div class="card-photo photo-debris" role="img" aria-label="Photo of a trailer loaded with old carpet, furniture and household junk"></div>
    <h3 class="card-head">Property<br>Cleanup</h3>
    <div class="card-body">
      <svg class="tick" viewBox="0 0 14 14"><circle cx="7" cy="7" r="7" fill="var(--ink)"/><path d="M3.8 7.2 L6 9.3 L10.2 4.9" fill="none" stroke="var(--paper)" stroke-width="1.7"/></svg>
      <p>Quick hauls, Debris<br>Removal, or full<br>cleanouts—no job<br>too big or small</p>
    </div>
  </article>

  <article class="abs card" style="top:921px;">
    <div class="card-photo photo-ground" role="img" aria-label="Photo of a graded gravel pad with stacked pavers, a compactor and a pickup truck"></div>
    <h3 class="card-head">Ground<br>Preparation</h3>
    <div class="card-body">
      <svg class="tick" viewBox="0 0 14 14"><circle cx="7" cy="7" r="7" fill="var(--ink)"/><path d="M3.8 7.2 L6 9.3 L10.2 4.9" fill="none" stroke="var(--paper)" stroke-width="1.7"/></svg>
      <p>Pad preparation,<br>Brush removal, and<br>Fire lines—making<br>properties safe,<br>Functional, and<br>Project-Ready</p>
    </div>
  </article>

  <footer class="abs contact-panel">
    <p class="call-line">Call or Text Today!</p>
    <div class="contact-row" style="top:33px;">
      <svg viewBox="0 0 14 14"><g fill="none" stroke="var(--ink)" stroke-width="1.2"><circle cx="7" cy="7" r="6.2"/><ellipse cx="7" cy="7" rx="2.8" ry="6.2"/><path d="M0.8 7 H13.2 M2 3.8 H12 M2 10.2 H12"/></g></svg>
      <span>www.brackwellyard.example</span>
    </div>
    <div class="contact-row" style="top:60px;">
      <svg viewBox="0 0 14 14"><rect x="0.5" y="2.5" width="13" height="9" fill="var(--ink)"/><path d="M0.8 3 L7 8 L13.2 3" fill="none" stroke="var(--paper)" stroke-width="1"/></svg>
      <span>sales@brackwellyard.example</span>
    </div>
  </footer>

  <svg class="abs phone-block" viewBox="0 0 380 52" aria-label="Phone (555) 014-7293">
    <circle cx="26" cy="26" r="24" fill="none" stroke="var(--paper)" stroke-width="1.6"/>
    <path d="M19 16 Q16 17 17 21 Q20 30 29 35 Q33 37 35 33 L32 29 L29 31 Q24 28 22 23 L24 20 Z" fill="var(--paper)"/>
    <path d="M28 15 Q35 16 37 23 M28 19 Q32 20 33 24" fill="none" stroke="var(--paper)" stroke-width="1.6" stroke-linecap="round"/>
    <text x="76" y="38" font-size="34" textLength="290" lengthAdjust="spacingAndGlyphs">(555) 014-7293</text>
  </svg>

</main>
</body>
</html>
```